Brindlewick Solutions Ltd

I'd like to create a company letterhead for the attached logo in word format.

I'd like to emphasis the icon in large translucent state from the left corner and ensure that the letterhead colouring matches the colour palette of the current logo with a contrast so it's clear to see. I've attached a copy of our sister company page on the app for reference.

```html
<!DOCTYPE html>
<html lang="en">
<head>
<meta charset="utf-8">
<title>Brindlewick Solutions Ltd – Letterhead</title>
<link rel="stylesheet" href="https://fonts.googleapis.com/css2?family=Arimo&family=Montserrat:wght@500&family=Mulish:wght@700;800&family=Open+Sans:wght@400&display=swap">
<style>
  :root {
    --backdrop: #e3e3e3;
    --paper: #ffffff;
    --brand-teal: #17bfa8;
    --brand-tint: #eef9f8;
    --ink: #555555;
    --ink-soft: #8e8e8e;
    --rule: #bdbdbd;
  }
  * { margin: 0; padding: 0; box-sizing: border-box; }
  html, body {
    width: 1200px;
    height: 1200px;
    overflow: hidden;
    background: var(--backdrop);
  }
  .letterhead {
    position: absolute;
    left: 233px;
    top: 81px;
    width: 734px;
    height: 1037px;
    overflow: hidden;
    background: var(--paper);
    color: var(--ink);
    font-family: "Arimo", Arial, sans-serif;
    box-shadow: 1px 2px 3px rgba(0,0,0,0.35);
  }
  .brand-watermark {
    position: absolute;
    left: -165px;
    top: 115px;
    width: 808px;
    height: 808px;
    border-radius: 50%;
    background: var(--brand-tint);
  }
  .brand {
    position: absolute;
    left: 65px;
    top: 44px;
    display: flex;
    align-items: center;
    gap: 12px;
  }
  .brand-dot {
    width: 66px;
    height: 66px;
    border-radius: 50%;
    background: var(--brand-teal);
  }
  .brand-name {
    font-family: "Montserrat", sans-serif;
    font-weight: 500;
    font-size: 26px;
    line-height: 29px;
    color: var(--brand-teal);
  }
  .divider {
    position: absolute;
    top: 57px;
    width: 1px;
    height: 42px;
    background: var(--rule);
  }
  .divider--first { left: 353px; }
  .divider--second { left: 502px; }
  .address {
    position: absolute;
    left: 390px;
    top: 52px;
    font-size: 12px;
    line-height: 16.7px;
    color: var(--ink-soft);
    font-style: normal;
  }
  .contact {
    position: absolute;
    left: 537px;
    top: 52px;
    list-style: none;
    font-size: 12px;
    line-height: 16.7px;
    color: var(--ink-soft);
  }
  .contact li {
    display: flex;
    align-items: center;
    gap: 6px;
  }
  .contact svg { width: 10px; height: 10px; flex: none; }
  .salutation {
    position: absolute;
    left: 67px;
    top: 318px;
    font-family: "Mulish", sans-serif;
    font-weight: 800;
    font-size: 16.8px;
    color: var(--ink);
  }
  .body-copy p {
    position: absolute;
    left: 65px;
    font-size: 12.8px;
    line-height: 15px;
    white-space: nowrap;
    color: var(--ink);
  }
  .body-copy span { display: block; }
  .closing {
    position: absolute;
    left: 67px;
    top: 678px;
    font-family: "Mulish", sans-serif;
    font-weight: 700;
    font-size: 10px;
    color: var(--ink);
  }
  .signature {
    position: absolute;
    left: 85px;
    top: 726px;
    font-family: "Open Sans", sans-serif;
    font-size: 18px;
    letter-spacing: -1.2px;
    color: var(--ink);
  }
</style>
</head>
<body>
  <main class="letterhead">
    <div class="brand-watermark" role="img" aria-label="Large faint brand symbol watermark rising from the left edge"></div>

    <header>
      <div class="brand">
        <div class="brand-dot"></div>
        <div class="brand-name">Brindlewick<br>Solutions Ltd</div>
      </div>
      <div class="divider divider--first"></div>
      <address class="address">
        Your address<br>city<br>state, ZIP 0000
      </address>
      <div class="divider divider--second"></div>
      <ul class="contact">
        <li>
          <svg viewBox="0 0 10 10" aria-hidden="true"><path fill="#17bfa8" d="M2.2 0.8l1.4 1.6-0.8 1.1c0.6 1.3 1.4 2.1 2.7 2.7l1.1-0.8 1.6 1.4-0.9 1.6C4.4 8.2 1.8 5.6 0.6 1.7z"/></svg>
          123-456-2100
        </li>
        <li>
          <svg viewBox="0 0 10 10" aria-hidden="true"><rect x="0" y="2" width="10" height="6.5" fill="#17bfa8"/><path d="M0.5 2.5L5 5.8 9.5 2.5" fill="none" stroke="#fff" stroke-width="0.9"/></svg>
          youremail@mailhost.com
        </li>
        <li>
          <svg viewBox="0 0 10 10" aria-hidden="true"><circle cx="5" cy="5" r="4.6" fill="#17bfa8"/><path d="M0.6 5h8.8M5 0.4c-2 2.6-2 6.6 0 9.2M5 0.4c2 2.6 2 6.6 0 9.2" fill="none" stroke="#fff" stroke-width="0.7"/></svg>
          www.yourwebsite.com
        </li>
      </ul>
    </header>

    <h1 class="salutation">Dear Mr. Smith,</h1>

    <section class="body-copy">
      <p style="top:367px">
        <span>Lorem ipsum dolor sit amet, consectetuer adipiscing elit, sed diam nonmmy nibh euismod tincidunt ut laor</span>
        <span>eet dolore magna aliquam erat volutpat. Ut wisi enim ad minim veniam, quis nostrud exerci tationmcorper</span>
        <span>suscipit lobortis nisl ut aliquip ex ea commodo consequat. Duis autem vel eum iriure dolor in hendrerit in</span>
        <span>vulputate velit esse molestie consequat, vel illum dolore eu feugiat</span>
      </p>
      <p style="top:441px">
        <span>Rorem ipsum dolor sit amet, consectetuer adipiscing elit, sed diam nonmmy nibh euismod tincidunt ut laor</span>
        <span>eet dolore magna aliquam erat volutpat. Ut wisi enim ad minim veniam, quis nostrud exerci tationmcorper</span>
        <span>suscipit lobortis nisl ut aliquip ex ea commodo consequat. Duis autem vel eum iriure dolor in hendrerit in</span>
        <span>vulputate velit esse molest</span>
      </p>
      <p style="top:515px">
        <span>Dorem ipsum dolor sit amet, consectetuer adipiscing elit, sed diam nonmmy nibh euismod tincidunt ut laor</span>
        <span>eet dolore magna aliquam erat volutpat. Ut wisi enim ad minim veniam, quis nostrud exerci tationmcorper</span>
        <span>suscipit lobortis nisl ut aliquip ex ea commodo consequat. Duis autem vel eum iriure dolor in hendrerit in</span>
        <span>suscipit lobortis nisl ut aliquip ex ea commodo consequat. Duis autem vel eum iriure dolor in hendrerit in</span>
        <span>vulputate velit esse molestie consequat, vel illum</span>
      </p>
      <p style="top:603px">
        <span>Sorem ipsum dolor sit amet, consectetuer adipiscing elit, sed diam nonmmy nibh euismod tincidunt ut laor</span>
        <span>eet dolore magna aliquam erat volutpat. Ut wisi enim ad minim veniam, quis nostrud exerci tationmcorper</span>
        <span>suscipit lobortis nisl ut aliquip ex ea commodo consequat. Duis autem vel eum iriure dolor in</span>
      </p>
    </section>

    <p class="closing">Sincerely,</p>
    <p class="signature">Rowan j ashby</p>
  </main>
</body>
</html>
```